design a construction company business card

Design business card around our logo. Card must have all the typical info: name, title, address, phone, email, business name, etc. Somewhere on the card I would like to see our motto "Grounded in Trust... Driven by Dedication." Consider adding a splash of bright orange to the card to complement the blues and silvers/grays in the logo. We are open to metallic inks, textures, etc. We would like to see options on both light and dark backgrounds. The font in the logo is Euro Technic Extended Regular.

```html
<!DOCTYPE html>
<html lang="en">
<head>
<meta charset="utf-8">
<title>Kestrel Contracting – Business Cards</title>
<link href="https://fonts.googleapis.com/css2?family=Zilla+Slab:wght@400;600;700&display=swap" rel="stylesheet">
<style>
  :root {
    --page: #f7f7f7;
    --card-dark: #231f20;
    --card-light: #ffffff;
    --blue: #1e63b8;
    --blue-deep: #22399a;
    --blue-bright: #1a78c8;
    --grey: #8a8b8d;
    --grey-light: #a7a9ac;
    --ink: #2b2b2b;
  }
  * { margin: 0; padding: 0; box-sizing: border-box; }
  html, body { width: 1200px; height: 754px; overflow: hidden; background: var(--page); }
  body { position: relative; font-family: "Zilla Slab", Georgia, serif; }

  .card { position: absolute; top: 226px; height: 302px; box-shadow: 0 10px 24px rgba(0,0,0,.28); overflow: hidden; }
  .card--front { left: 50px; width: 528px; background: var(--card-dark); }
  .card--back { left: 621px; width: 531px; background: var(--card-light); }

  /* front */
  .front-name { position: absolute; left: 30px; top: 172px; font-weight: 700; font-size: 54px; line-height: 1; letter-spacing: 7px; color: var(--blue); }
  .front-sub { position: absolute; left: 30px; top: 232px; font-size: 19px; letter-spacing: 1px; color: var(--grey-light); }
  .motto { position: absolute; left: 32px; top: 255px; font-size: 15px; color: var(--grey-light); }
  .front-band { position: absolute; left: 25px; top: 275px; width: 349px; height: 8px; background: linear-gradient(90deg, var(--blue-deep), var(--blue)); }
  .front-bar { position: absolute; left: 461px; top: 17px; width: 16px; height: 266px; background: linear-gradient(180deg, var(--blue-bright), var(--blue-deep)); }

  /* back */
  .address { position: absolute; left: 27px; top: 51px; font-size: 14px; line-height: 21px; color: var(--blue); }
  .back-name { position: absolute; right: 29px; top: 66px; text-align: right; font-weight: 700; font-size: 30px; line-height: 1; letter-spacing: 2px; color: var(--blue); }
  .back-name small { display: block; font-size: 12px; font-weight: 700; letter-spacing: .8px; margin-top: 5px; }
  .back-grey { position: absolute; left: 27px; top: 164px; width: 10px; height: 120px; background: var(--grey); }
  .back-blue { position: absolute; left: 66px; top: 132px; width: 10px; height: 152px; background: linear-gradient(180deg, var(--blue-bright), var(--blue-deep)); }
  .back-band { position: absolute; left: 66px; bottom: 18px; right: 0; height: 8px; background: linear-gradient(90deg, var(--blue), var(--blue-deep)); }
  .back-tab { position: absolute; right: 0; top: 171px; width: 12px; height: 33px; background: var(--blue); }

  .contact { position: absolute; left: 115px; top: 168px; list-style: none; }
  .contact li { display: flex; align-items: center; height: 21.5px; font-size: 14px; color: var(--ink); }
  .contact svg { width: 15px; height: 15px; margin-right: 7px; fill: var(--blue); }

  .person { position: absolute; right: 29px; top: 170px; text-align: right; }
  .person-name { font-weight: 700; font-size: 20px; color: var(--blue); line-height: 1.1; }
  .person-title { font-size: 12px; color: var(--ink); }
</style>
</head>
<body>

<section class="card card--front">
  <div class="front-name">KESTREL</div>
  <div class="front-sub">—CONTRACTING, INC.—</div>
  <p class="motto">Grounded in Trust... Driven by Dedication</p>
  <div class="front-band"></div>
  <div class="front-bar"></div>
</section>

<section class="card card--back">
  <p class="address">118/4 Harbour Rd, Kellwood<br>NSW 2071, NY</p>
  <div class="back-name">KESTREL<small>CONTRACTING, INC.</small></div>

  <div class="back-grey"></div>
  <div class="back-blue"></div>
  <div class="back-band"></div>
  <div class="back-tab"></div>

  <ul class="contact">
    <li><svg viewBox="0 0 24 24" aria-hidden="true"><path d="M6.6 10.8a15.1 15.1 0 0 0 6.6 6.6l2.2-2.2c.3-.3.7-.4 1-.2 1.1.4 2.3.6 3.6.6.6 0 1 .4 1 1V20c0 .6-.4 1-1 1A17 17 0 0 1 3 4c0-.6.4-1 1-1h3.5c.6 0 1 .4 1 1 0 1.3.2 2.5.6 3.6.1.3 0 .7-.2 1z"/></svg>(02) 5550 1842</li>
    <li><svg viewBox="0 0 24 24" aria-hidden="true"><path d="M7 1h10a2 2 0 0 1 2 2v18a2 2 0 0 1-2 2H7a2 2 0 0 1-2-2V3a2 2 0 0 1 2-2zm0 3v14h10V4zm5 15.5a1.2 1.2 0 1 0 0 2.4 1.2 1.2 0 0 0 0-2.4z"/></svg>0400 555 123</li>
    <li><svg viewBox="0 0 24 24" aria-hidden="true"><path d="M2 5h20v2l-10 6L2 7zm0 4 10 6 10-6v10H2z"/></svg>info@kestrelcontracting.com</li>
    <li><svg viewBox="0 0 24 24" aria-hidden="true"><path d="M12 2a10 10 0 1 0 0 20 10 10 0 0 0 0-20zm-1 17.9A8 8 0 0 1 4.2 10L9 14.8v1a2 2 0 0 0 2 2zm6.9-2.5A2 2 0 0 0 16 16h-1v-3a1 1 0 0 0-1-1H8v-2h2a1 1 0 0 0 1-1V7h2a2 2 0 0 0 2-2v-.4a8 8 0 0 1 2.9 12.8z"/></svg>www.kestrelcontracting.com</li>
  </ul>

  <div class="person">
    <div class="person-name">Dana Whitlock</div>
    <div class="person-title">Founder | CEO</div>
  </div>
</section>

</body>
</html>
```